Enrollment Campaign

We need a flyer design for our school's enrollment campaign. Our school website is www.tbvacademy.net.

The flyer should be double sided.

I want the reader to get the following messages:
1. Montessori graduates are leading the top companies of our time.
2. We are an accredited Montessori school.
3. Enrollment is open now for all four programs:
a) Toddler: 18months (or as soon as the child is able to walk) - 3 years
b) CASA: Preschool to Senior Kindergarten (3 years to 6 years)
c) Elementary: Grades 1 to 6
d) Junior High: Grades 7 to 8
4) Our contact information:
website, email:info@tbvacademy.net, phone: 647 382 5146
5) Call for Action: Book a Tour! (there is a button on our website to book a tour)
6) In the languages punjabi, hindi and italian, I wouldn't readers to know that we offer their faith and cultural education as well.
7) Fees for children under age of 6 can be claimed in Taxes as day care expense. So, there is no reason to miss providing our children the best that we can in education.
Updates

Please note my updates to my brief in the "must have" section. Also, I have added some pics that can be used. Please note that I don't have one pic (the farming one referred to in my brief). I will really appreciate if you can kindly update your design accordingly.

Reason: Because of my recent update to the brief, some designers need some time to adjust their designs. I really appreciate your patience and kind consideration for my project. Thank you!

Industry/Entity Type

Education

Colors

Designer to choose colors to be used in the design.

Requirements
Must have
• Must have a unique design. I don't want a typical flyer. The design should be unique and memorable.

One of the main pics that I need is for illustrating a key feature of our new Junior High program that we are starting in August 2015. The key feature is that children are going to be operating a 'greenhouse', growing organic produce and will also be preparing their daily lunch from scratch. So, show a pic of a 13-14year old farming or something.

```html
<!DOCTYPE html>
<html lang="en">
<head>
<meta charset="utf-8">
<title>TBV Academy – Enrollment Flyer</title>
<link rel="stylesheet" href="https://fonts.googleapis.com/css2?family=Didact+Gothic&family=Nunito+Sans:wght@400;700;800&display=swap">
<style>
:root{
  --backdrop:#d9d9d9;
  --paper:#f7f7f5;
  --red:#c0272d;
  --orange:#f39a1e;
  --blue:#1b75bc;
  --green:#6cb33f;
  --heading-blue:#1e7bc4;
  --text-grey:#555a5e;
  --text-dark:#333638;
  --table-blue:#cfe3ef;
  --table-line:#9bbcd0;
  --contact-blue:#d9e9f4;
}
*{margin:0;padding:0;box-sizing:border-box}
html,body{width:847px;height:1200px;overflow:hidden}
body{background:var(--backdrop);position:relative;font-family:"Didact Gothic",sans-serif;color:var(--text-dark)}
.page{position:absolute;left:248px;width:330px;height:428px;background:var(--paper);overflow:hidden;box-shadow:0 2px 6px rgba(0,0,0,.12)}
.page--front{top:66px}
.page--back{top:668px}
.color-stripe{position:absolute;left:0;width:100%;height:6px;display:flex}
.color-stripe span{flex:1}
.color-stripe .s-red{background:var(--red)}
.color-stripe .s-orange{background:var(--orange)}
.color-stripe .s-blue{background:var(--blue)}
.color-stripe .s-green{background:var(--green)}

/* front */
.front-tagline{position:absolute;left:19px;top:66px;font-size:11.5px;line-height:15px;color:var(--red)}
.blocks-art{position:absolute;background:linear-gradient(135deg,#f2c230 0%,#e0503a 35%,#3d8fd0 65%,#7ab648 100%);opacity:.85;border-radius:2px}
.front-blocks{left:212px;top:20px;width:80px;height:68px}
.front-stripe{top:104px}
.hero-photo{position:absolute;left:0;top:110px;width:100%;height:261px;background:linear-gradient(180deg,#1f5a4c 0%,#25614f 55%,#b5743a 82%,#d49a5a 100%)}
.brand{position:absolute;left:0;right:0;top:393px;display:flex;align-items:center;justify-content:center;gap:6px}
.brand-dot{width:12px;height:12px;border-radius:50%;background:var(--heading-blue)}
.brand-name{font-family:"Didact Gothic",sans-serif;font-size:17px;color:var(--heading-blue)}

/* back */
.back-blocks{left:38px;top:16px;width:40px;height:50px}
.accredited{position:absolute;left:34px;top:74px;font-size:11px;line-height:12px;color:var(--text-dark)}
.accredited strong{display:block;font-family:"Nunito Sans",sans-serif;font-weight:800;font-size:10px;letter-spacing:.3px}
.rule{position:absolute;left:34px;width:114px;height:2px;background:var(--green)}
.enroll-heading{position:absolute;left:34px;top:116px;font-family:"Nunito Sans",sans-serif;font-weight:800;font-size:14.5px;line-height:16.5px;color:var(--heading-blue);letter-spacing:.2px}
.programs{position:absolute;left:34px;top:199px;width:114px;border-collapse:collapse;background:var(--table-blue);font-size:7px;line-height:8.5px}
.programs th{font-family:"Nunito Sans",sans-serif;font-weight:700;font-size:7.5px;text-align:left;vertical-align:top;padding:5px 4px;width:52px;color:var(--text-dark)}
.programs td{vertical-align:top;padding:5px 4px;color:var(--text-grey)}
.programs tr+tr th,.programs tr+tr td{border-top:1px dashed var(--table-line)}
.programs th+td{border-left:1px solid var(--table-line)}
.kids-photo{position:absolute;left:34px;top:337px;width:114px;height:76px;background:linear-gradient(135deg,#f0c95a 0%,#e7a07a 45%,#8fb3d9 100%)}
.girl-photo{position:absolute;left:176px;top:0;width:141px;height:212px;background:linear-gradient(180deg,#caa27a 0%,#e2d6c6 45%,#eeeae4 70%,#d65a86 100%)}
.tour-ribbon{position:absolute;left:176px;top:199px;width:140px;height:22px;background:var(--red);color:#fff;padding:3px 6px;clip-path:polygon(0 0,100% 0,94% 50%,100% 100%,0 100%)}
.tour-ribbon strong{display:block;font-family:"Nunito Sans",sans-serif;font-size:7.5px;line-height:8px}
.tour-ribbon span{display:block;font-size:5.6px;line-height:7px}
.faith-note{position:absolute;left:178px;top:230px;width:136px;font-size:8px;line-height:10.5px;color:var(--red)}
.tax-note{position:absolute;left:178px;top:277px;width:136px;font-size:7.3px;line-height:9.5px;color:var(--text-grey)}
.contact{position:absolute;left:176px;top:331px;width:140px;height:82px;background:var(--contact-blue);border-radius:10px;padding:8px 10px}
.contact::before{content:"";position:absolute;right:24px;top:-7px;border:7px solid transparent;border-bottom-color:var(--contact-blue);border-top:0}
.contact h2{font-family:"Nunito Sans",sans-serif;font-weight:700;font-size:9px;color:var(--heading-blue);margin-bottom:4px}
.contact ul{list-style:none;font-size:8px;line-height:10.5px;color:var(--text-dark)}
.contact li{display:flex;align-items:flex-start;gap:5px}
.contact svg{flex:none;width:7px;height:7px;margin-top:2px;fill:var(--heading-blue)}
.back-stripe{bottom:0}
</style>
</head>
<body>

<section class="page page--front" aria-label="Flyer front">
  <p class="front-tagline">Montessori graduates are leading<br>the top companies of our time</p>
  <div class="blocks-art front-blocks" role="img" aria-label="Stacked wooden toy building blocks"></div>
  <div class="color-stripe front-stripe"><span class="s-red"></span><span class="s-orange"></span><span class="s-blue"></span><span class="s-green"></span></div>
  <div class="hero-photo" role="img" aria-label="Back to school scene: red backpack, alarm clock, pencils, apple and notebooks in front of a chalkboard reading Back to School"></div>
  <div class="brand"><span class="brand-dot"></span><span class="brand-name">TBV Academy</span></div>
</section>

<section class="page page--back" aria-label="Flyer back">
  <div class="blocks-art back-blocks" role="img" aria-label="Small tower of toy building blocks"></div>
  <p class="accredited">We are an accredited<strong>MONTESSORI SCHOOL</strong></p>
  <div class="rule" style="top:106px"></div>
  <h1 class="enroll-heading">ENROLLMENT<br>IS OPEN NOW<br>FOR ALL FOUR<br>PROGRAMS</h1>
  <div class="rule" style="top:187px"></div>
  <table class="programs">
    <tr><th>Toddler</th><td style="height:45px">18months (or as soon as the child is able to walk) ~ 3 years</td></tr>
    <tr><th>CASA</th><td style="height:37px">Preschool to Senior Kindergarten (3 years to 6 years)</td></tr>
    <tr><th>Elementary</th><td>Grades 1 to 6</td></tr>
    <tr><th>Junior High</th><td>Grades 7 to 8</td></tr>
  </table>
  <div class="kids-photo" role="img" aria-label="Three smiling young students giving thumbs up"></div>

  <div class="girl-photo" role="img" aria-label="Young girl building a tower with Montessori cylinder blocks on the classroom floor"></div>
  <div class="tour-ribbon"><strong>Call for Action: Book a Tour !</strong><span>there is a button on our website to book a tour</span></div>
  <p class="faith-note">In the languages punjabi, hindi and italian, I wouldn't readers to know that we offer their faith and cultural education as well.</p>
  <p class="tax-note">Fees for children under age of 6 can be claimed in Taxes as day care expense. So, there is no reason to miss providing our children the best that we can in education.</p>
  <div class="contact">
    <h2>Our contact information</h2>
    <ul>
      <li><svg viewBox="0 0 10 10"><circle cx="5" cy="5" r="4.2" fill="none" stroke="currentColor" style="stroke:var(--heading-blue)" stroke-width="1.4"/><circle cx="5" cy="5" r="1.6"/></svg>www.tbvacademy.net</li>
      <li><svg viewBox="0 0 10 10"><rect x="0.5" y="2" width="9" height="6.5" rx="1"/></svg>info@tbvacademy.net</li>
      <li><svg viewBox="0 0 10 10"><path d="M2 0.5l2 2.2-1 1.3a6 6 0 0 0 3 3l1.3-1 2.2 2-1.3 1.5C4.5 9.5 .5 5.5 .6 1.8z"/></svg>647-382-5146</li>
      <li><svg viewBox="0 0 10 10"><path d="M5 .5L.5 4.8h1.4V9.5h2.4V6.6h1.4v2.9h2.4V4.8h1.4z"/></svg><span>18-2270 Maple Crest Drive<br>Brampton, ON, L6R3K9</span></li>
    </ul>
  </div>
  <div class="color-stripe back-stripe"><span class="s-red"></span><span class="s-orange"></span><span class="s-blue"></span><span class="s-green"></span></div>
</section>

</body>
</html>
```